Simple templates for management consulting firm

Vireo Advisors is a management consulting firm based in the DC area. We have all the basic templates but would like to tweak them so they look consistent.

Check us out at www.vireoadvisors.example

For this project we would like to get
a tweaked powerpoint template (header should be up)
a letter template for letters
a fax template

Current templates and our logo are attached.
Updates

We just increased the budget of this project.

We got questions about the project. Here are our thoughts on this one:

Please include the logo into the fax template. If you find improvements in the layout then feel free to make those. Let's not overthink this too much. Keep it simple :)

We like The powerpoint concept as is. The slide titles are for some reasons on the bottom. It seems to irritate some folks. If you can switch the slide titles to the top, keep the look and feel of the slides and work in the logo then that would be fantastic.

The letter head should include the following

Vireo Advisors, LLC Box 5827, Great Falls, VA 20471 Phone 703 555-0148, Fax 703 555 0193, www.vireoadvisors.example and the logo.

Again, let's keep it simple.

Thank you for considering this project.

We just realize that we are not necessarily inisting to use the red in the slides.
Any approach that would work with the logo will be considered.

Thanks for your creativity.

Target Market(s)

tech companies, Meridian 400, venture capitalists

Industry/Entity Type

Management Consulting

Requirements
Must have
• Keep it simple please

```html
<!DOCTYPE html>
<html lang="en">
<head>
<meta charset="utf-8">
<title>Vireo Advisors – Slide Template</title>
<link href="https://fonts.googleapis.com/css2?family=PT+Sans+Narrow:wght@400;700&display=swap" rel="stylesheet">
<style>
  :root {
    --slide-center: #fbfbfb;
    --slide-edge: #c9c9c9;
    --gap: #ffffff;
    --ink-dark: #3f3f3f;
    --ink-mid: #5a5a5a;
    --ink-title: #666666;
    --rule: #9a9a9a;
    --mark-grey: #8f8f8f;
    --mark-gold: #c9a24a;
    --faint: rgba(150,150,150,0.28);
  }
  * { margin: 0; padding: 0; box-sizing: border-box; }
  html, body { width: 871px; height: 1200px; overflow: hidden; background: var(--gap); }
  body { font-family: "PT Sans Narrow", "Arial Narrow", sans-serif; color: var(--ink-mid); position: relative; }

  .slide {
    position: absolute; left: 0; width: 871px; overflow: hidden;
    background: radial-gradient(ellipse 70% 65% at 50% 45%, var(--slide-center) 0%, #ececec 55%, var(--slide-edge) 100%);
  }
  .slide--title { top: 0; height: 590px; }
  .slide--agenda { top: 598px; height: 602px; }

  .brand { position: absolute; display: flex; align-items: center; }
  .brand--title { left: 208px; top: 218px; gap: 22px; }
  .brand__dot { width: 124px; height: 124px; border-radius: 50%; background: var(--mark-gold); }
  .brand__name { font-weight: 400; font-size: 74px; color: var(--mark-grey); letter-spacing: 1px; white-space: nowrap; }

  .brand--faint { left: 70px; top: 220px; gap: 26px; }
  .brand--faint .brand__dot { width: 180px; height: 180px; background: var(--faint); }
  .brand--faint .brand__name { font-size: 110px; color: var(--faint); }

  .presenter { position: absolute; top: 438px; width: 100%; text-align: center; }
  .presenter__name { font-weight: 700; font-size: 52px; line-height: 1; color: var(--ink-dark); }
  .presenter__role { font-size: 27px; line-height: 1.2; color: var(--ink-dark); margin-top: 2px; }

  .footer { position: absolute; left: 0; width: 100%; text-align: center; }
  .footer__rule { position: absolute; left: 42px; right: 60px; top: 0; border-top: 1px solid var(--rule); }
  .footer__text { position: absolute; left: 20px; right: 20px; top: 8px; font-size: 14.5px; line-height: 13px; color: var(--ink-dark); }
  .slide--title .footer { top: 545px; }
  .slide--agenda .footer { top: 554px; }

  .slide__heading { position: absolute; top: 26px; width: 100%; text-align: center; font-weight: 700; font-size: 54px; color: var(--ink-title); }

  .agenda { position: absolute; left: 58px; top: 162px; list-style: none; }
  .agenda__item { position: relative; padding-left: 16px; font-size: 34px; line-height: 46px; color: var(--ink-mid); }
  .agenda__item::before { content: ""; position: absolute; left: 0; top: 21px; width: 9px; height: 5px; border-radius: 2px; background: var(--ink-mid); }
  .agenda__sub { list-style: none; margin: -4px 0 2px 41px; }
  .agenda__sub li { font-weight: 700; font-size: 29px; line-height: 36px; color: var(--ink-mid); }
</style>
</head>
<body>

<section class="slide slide--title">
  <div class="brand brand--title">
    <span class="brand__dot"></span>
    <span class="brand__name">Vireo Advisors</span>
  </div>
  <div class="presenter">
    <div class="presenter__name">Daniel Harwick</div>
    <div class="presenter__role">Managing Partner</div>
  </div>
  <footer class="footer">
    <div class="footer__rule"></div>
    <p class="footer__text">Copyright © 2012 by Vireo Advisors, LLC. All rights reserved. This document contains confidential and proprietary information and may not be<br>reproduced, in whole or in part, without express written permission from Vireo Advisors, LLC.</p>
  </footer>
</section>

<section class="slide slide--agenda">
  <div class="brand brand--faint" aria-hidden="true">
    <span class="brand__dot"></span>
    <span class="brand__name">Vireo Advisors</span>
  </div>
  <h1 class="slide__heading">Agenda</h1>
  <ul class="agenda">
    <li class="agenda__item">Jumpstart Your Business
      <ul class="agenda__sub">
        <li>Mastering the Sale</li>
        <li>Getting Projects Done</li>
        <li>Turnaround</li>
      </ul>
    </li>
    <li class="agenda__item">Vireo Advisor’s Engagement Model</li>
    <li class="agenda__item">About Lukas Brenner</li>
  </ul>
  <footer class="footer">
    <div class="footer__rule"></div>
    <p class="footer__text">Copyright © 2012 by Vireo Advisors, LLC. All rights reserved. This document contains confidential and proprietary information and may not be<br>reproduced, in whole or in part, without express written permission from Vireo Advisors, LLC.</p>
  </footer>
</section>

</body>
</html>
```